Ridgeline Journeys business card

please see website
www.ridgelinejourneys.comau

info needed on card
Curtis Halvey
Ph
email
Adventure Riding GPS trails

please use my logo and colours off my site

Curtis Halvey
curtis@ridgelinejourneys.com

```html
<!DOCTYPE html>
<html lang="en">
<head>
<meta charset="utf-8">
<title>Ridgeline Journeys – Business Card</title>
<link href="https://fonts.googleapis.com/css2?family=Open+Sans:wght@400;600;700&display=swap" rel="stylesheet">
<style>
  :root {
    --stage: #000000;
    --card: #38393b;
    --accent: #f5e11a;
    --text-light: #ffffff;
    --mark-grey: #6a6b6d;
    --divider: #2c2d2f;
  }
  html, body {
    margin: 0;
    padding: 0;
    width: 1200px;
    height: 900px;
    overflow: hidden;
    background: var(--stage);
    font-family: "Open Sans", Arial, sans-serif;
  }
  .stage {
    position: relative;
    width: 1200px;
    height: 900px;
  }
  .card {
    position: absolute;
    top: 271px;
    width: 456px;
    height: 281px;
    border-radius: 14px;
    background: var(--card);
    overflow: hidden;
  }
  .card--front { left: 137px; }
  .card--back { left: 626px; }

  /* brand block */
  .brand {
    position: absolute;
    display: flex;
    align-items: center;
    gap: 10px;
    color: var(--text-light);
    font-weight: 700;
    line-height: 1.1;
  }
  .brand__dot {
    flex: none;
    border-radius: 50%;
    background: var(--mark-grey);
  }
  .card--front .brand {
    left: 60px;
    top: 104px;
    width: 160px;
    font-size: 17px;
  }
  .card--front .brand__dot { width: 22px; height: 22px; }
  .card--back .brand {
    left: 70px;
    top: 104px;
    font-size: 34px;
    letter-spacing: 0.5px;
  }
  .card--back .brand__dot { width: 34px; height: 34px; }

  .divider {
    position: absolute;
    left: 224px;
    top: 74px;
    width: 1px;
    height: 120px;
    background: var(--divider);
  }

  .person {
    position: absolute;
    left: 242px;
    top: 88px;
  }
  .person__name {
    margin: 0 0 12px;
    color: var(--accent);
    font-size: 15px;
    font-weight: 600;
  }
  .contact {
    list-style: none;
    margin: 0;
    padding: 0;
  }
  .contact__item {
    display: flex;
    align-items: center;
    gap: 6px;
    height: 19px;
    color: var(--text-light);
    font-size: 12.5px;
  }
  .contact__icon {
    width: 13px;
    height: 13px;
    flex: none;
  }

  .rule-caption {
    position: absolute;
    left: 0;
    right: 0;
    display: flex;
    align-items: center;
    gap: 6px;
    color: var(--accent);
    font-weight: 600;
  }
  .rule-caption::before,
  .rule-caption::after {
    content: "";
    flex: 1;
    height: 1px;
    background: var(--accent);
    opacity: 0.75;
  }
  .card--front .rule-caption { top: 223px; font-size: 13.5px; }
  .card--back .rule-caption { top: 221px; font-size: 12px; font-weight: 700; }
</style>
</head>
<body>
<main class="stage">

  <section class="card card--front" aria-label="Business card front">
    <div class="brand">
      <span class="brand__dot"></span>
      <span>Ridgeline Journeys</span>
    </div>
    <div class="divider"></div>
    <div class="person">
      <p class="person__name">Curtis Halvey</p>
      <ul class="contact">
        <li class="contact__item">
          <svg class="contact__icon" viewBox="0 0 13 13" aria-hidden="true">
            <rect width="13" height="13" rx="2" fill="var(--accent)"/>
            <path d="M3 4.5c0-1 .8-1.5 3.5-1.5S10 3.5 10 4.5v.8H8.3v-.8H4.7v.8H3z M4 6.3h5l1 3.7H3z" fill="#38393b"/>
          </svg>
          (044)-555-0192
        </li>
        <li class="contact__item">
          <svg class="contact__icon" viewBox="0 0 13 13" aria-hidden="true">
            <rect width="13" height="13" rx="2" fill="var(--accent)"/>
            <rect x="3" y="4" width="7" height="5" fill="#38393b"/>
          </svg>
          curtis@ridgelinejourneys.com
        </li>
        <li class="contact__item">
          <svg class="contact__icon" viewBox="0 0 13 13" aria-hidden="true">
            <rect width="13" height="13" rx="2" fill="var(--accent)"/>
            <path d="M4.5 8.5l4-4M5.5 6.5l-1.5 1.5a1.1 1.1 0 0 0 1.5 1.5l1.5-1.5M7.5 6.5L9 5a1.1 1.1 0 0 0-1.5-1.5L6 5" stroke="#38393b" stroke-width="1.1" fill="none" stroke-linecap="round"/>
          </svg>
          www.ridgelinejourneys.comau
        </li>
      </ul>
    </div>
    <p class="rule-caption" style="margin:0">Adventure Riding GPS trails</p>
  </section>

  <section class="card card--back" aria-label="Business card back">
    <div class="brand">
      <span class="brand__dot"></span>
      <span>Ridgeline<br>Journeys</span>
    </div>
    <p class="rule-caption" style="margin:0">www.ridgelinejourneys.comau</p>
  </section>

</main>
</body>
</html>
```